Construction material supplies company business card ****

1. Full company name “K T Masonry Works Ltd”
I am after a Business card design for the company as a whole. We are better known in Solomon Islands as “K T Masonry” for short.

We are a building materials supplier of
Ready Mixed Concrete, Bricks and Blocks,
Quarry products- gravel, aggregates, sand etc.
Cement distributor/retailer of reputable brands.
Other prefab concrete products. Culverts, wave breakers, concrete retaining blocks etc.

2. Competitive Advantage over Competition: Quality, efficient, professional, dependable, reliable

3. We want people to feel trust worthy, high quality, strong when they see our brand

5. No preference to color. Maybe more sturdy and corporate. Not fancy.

Industry/Entity Type

CONSTRUCTION SUPPLY

Contact Information for Business Card

Name, Position, office phone mob phone, email

Requirements
Must have
• the company logo
Nice to have
• would like to see a mixture of designs, of with logo only and also with simple graphic designs to bring out the company whilst still have the strong sturdy professional feeling

```html
<!DOCTYPE html>
<html lang="en">
<head>
<meta charset="utf-8">
<title>K T Masonry – Business Card</title>
<link rel="stylesheet" href="https://fonts.googleapis.com/css2?family=Roboto:wght@400;700&display=swap">
<style>
  :root {
    --backdrop: #93959a;
    --navy: #0f4466;
    --paper: #f0eff4;
    --white: #ffffff;
    --ink-grey: #4a4d52;
  }
  * { margin: 0; padding: 0; box-sizing: border-box; }
  html, body {
    width: 1200px; height: 900px; overflow: hidden;
    background: var(--backdrop);
    font-family: "Roboto", Arial, sans-serif;
  }
  .canvas { position: relative; width: 1200px; height: 900px; }
  .card {
    position: absolute; left: 363px; width: 475px; height: 271px;
  }
  .card--front { top: 145px; background: var(--navy); }
  .card--back { top: 484px; background: var(--paper); }

  .brand {
    position: absolute; display: flex; align-items: center; gap: 10px;
    font-weight: 700; letter-spacing: 1px; white-space: nowrap;
  }
  .brand__square { display: block; }
  .card--front .brand {
    left: 50%; top: 50%; transform: translate(-50%, -50%);
    color: var(--white); font-size: 30px;
  }
  .card--front .brand__square { width: 28px; height: 28px; background: var(--white); }
  .card--back .brand {
    left: 27px; top: 31px; color: var(--navy); font-size: 26px;
  }
  .card--back .brand__square { width: 24px; height: 24px; background: var(--navy); }

  .holder {
    position: absolute; right: 27px; top: 147px; text-align: right;
  }
  .holder__name {
    color: var(--navy); font-weight: 700; font-size: 14.5px; letter-spacing: 0.2px;
  }
  .holder__title {
    color: var(--ink-grey); font-size: 11px; margin-top: 6px;
  }
  .divider {
    position: absolute; left: 27px; top: 173px; width: 373px; height: 1px;
    background: var(--navy);
  }
  .contacts {
    position: absolute; left: 27px; top: 185px; list-style: none;
    color: var(--ink-grey); font-size: 11px; line-height: 15.3px;
  }
  .contacts li { display: flex; align-items: center; gap: 6px; }
  .contacts svg { width: 8px; height: 8px; fill: var(--navy); flex: none; }
</style>
</head>
<body>
<div class="canvas">
  <section class="card card--front" aria-label="Business card front">
    <div class="brand"><span class="brand__square"></span><span>K T MASONRY</span></div>
  </section>

  <section class="card card--back" aria-label="Business card back">
    <div class="brand"><span class="brand__square"></span><span>K T MASONRY</span></div>
    <div class="holder">
      <p class="holder__name">MARTIN KELLER</p>
      <p class="holder__title">Director</p>
    </div>
    <div class="divider"></div>
    <ul class="contacts">
      <li>
        <svg viewBox="0 0 8 8" aria-hidden="true"><path d="M2 0h4a1 1 0 0 1 1 1v6a1 1 0 0 1-1 1H2a1 1 0 0 1-1-1V1a1 1 0 0 1 1-1zm0 1v5h4V1z"/></svg>
        <span>555.201.4471</span>
      </li>
      <li>
        <svg viewBox="0 0 8 8" aria-hidden="true"><path d="M1.6 0.4 3 1.8 2.3 3a5 5 0 0 0 2.7 2.7L6.2 5 7.6 6.4 6.8 7.6C3.8 7.4 0.6 4.2 0.4 1.2z"/></svg>
        <span>555.310.2290</span>
      </li>
      <li>
        <svg viewBox="0 0 8 8" aria-hidden="true"><path d="M0 1.5h8v5H0zm0.6 0.6v0.3L4 4.6l3.4-2.2v-0.3z"/></svg>
        <span>mkeller@ktmasonry.com</span>
      </li>
      <li>
        <svg viewBox="0 0 8 8" aria-hidden="true"><path d="M4 0a4 4 0 1 1 0 8 4 4 0 0 1 0-8zm-0.5 1H3a3 3 0 0 0-2 2.5h2.4zm1 0 0.1 2.5H7A3 3 0 0 0 5 1zM1 4.5A3 3 0 0 0 3 7h0.5l-0.1-2.5zm3.5 0L4.5 7H5a3 3 0 0 0 2-2.5z"/></svg>
        <span>www.ktmasonry.com</span>
      </li>
    </ul>
  </section>
</div>
</body>
</html>
```